The Fresh Start Set! A Deck of cards to help you get over your ex.

I'm creating a deck of cards - 52 cards, 4 designs total. This contest is for the design of 4 cards, front and back. The winner will (most likely) be hired to fill out the other cards in the same style. I've included a template to give you a sense of what I imagine and also the physical sizes and specs of each card. (standard Poker size cards) I'll be creating about 20 different decks so there's a potential for you to be my long-term designer!

This is the fresh start set!

This deck of cards is designed to help you get over a breakup.
The idea is that after working through the deck, many of the stories and attachments to previous relationships will be resolved or broken.

There are 4 different sections, like the four suits in a Deck.
Each sections Addresses a different facet of relationships in general:

Blue - Your relationship with Yourself
Red - Your relationship to your partner
Purple - Your relationship to relationships
Green - Your relationship to your future

Each card:

FRONT - Headline (or theme) and a question
Back - A follow-up question and a QR code.
(QR code can be located anywhere on the back and will be unique to each card. It can also be a square shape or a round shape, your choice, and any color or a gradient.)

All other design elements are up to the artist.

They’re designed to give you an area to work on,
or present you with a conversation that might give you insights.
So the intention is that each of these cards is that you’ll do the work, or somehow take action on.

I’m looking for a feel that will work in a professional coaching
environment, or professional style-seminar or workshop.

I want people to feel like they want to carry around individual cards that speak to them in their wallets as a reminder, or post a card on their mirror as they work on a certain issue, or maybe glue a card into their journal.

So I’d like them to be visually appealing without going overboard.
Anything too plain, and the cards will look like cheap flash cards and won’t be valued.
Anything too elaborate, (like tarot-style illustrations) will take
away from the power of the question.

Low designer entries

Hello everyone! I've recieved a few good designs that give me some real hope that I'll find the right feel and deign for my coaching cards! However I would love to see some designs from some off the more experienced designers, so I've increased the prize amount and added a reward for second place! I've also extennded this project out for another 5 days to give more people a chance to submit their designs. If you have an idea, I'd love to see it! Happy designing!

Target Market(s)

Self-Help, Self-improvement, Relationship counselors, and people who are into transformational coaching.

Industry/Entity Type

Life Coaching

Font styles to use
Serif
Sans Serif

Colors
6b449b
0655a3
00a990
ec1f27

Requirements
Must have
• 1) A topic and a question on the front (with a darker background)
2) A question and a QR code on the back (with a ligher background)

One Blue card, one red card, one purple card and one green card.

The deck is a breakup deck, the theme is about getting over your ex, and that must communicate in the design.

The question must be the star of the card. The question must stand out on each side.
Nice to have
• Something that personalizes each card. Maybe even an illustration.
Should not have
• Overly simple, text only is too little.

Overly illustrated, like a tarot deck, is too much.

```html
<!DOCTYPE html>
<html lang="en">
<head>
<meta charset="utf-8">
<title>The Fresh Start Set – Card Concepts</title>
<link rel="stylesheet" href="https://fonts.googleapis.com/css2?family=Playfair+Display:ital@1&family=Poppins:wght@400;600&display=swap">
<style>
  :root {
    --blue: #0e56a4;
    --purple: #6b449b;
    --green: #16ad95;
    --red: #ec1f2d;
    --ink: #141414;
    --paper: #ffffff;
    --cut: #222222;
    --sketch: #e9e6e2;
  }
  * { margin: 0; padding: 0; box-sizing: border-box; }
  html, body { width: 1200px; height: 1156px; overflow: hidden; background: var(--paper); }
  .sheet { position: relative; width: 1200px; height: 1156px; color: var(--ink); }

  .card {
    position: absolute;
    width: 333px; height: 238px;
    border: 1.6px dashed var(--cut);
    border-radius: 16px;
  }
  .card-1 { left: 63px;  top: 55px; }
  .card-2 { left: 431px; top: 55px; }
  .card-3 { left: 803px; top: 55px; }
  .card-4 { left: 64px;  top: 333px; }
  .card-5 { left: 430px; top: 333px; }
  .card-6 { left: 798px; top: 332px; }
  .card-7 { left: 64px;  top: 598px; }
  .card-8 { left: 64px;  top: 859px; }

  .suit-band {
    position: absolute;
    height: 78px;
    overflow: hidden;
  }
  .suit-title {
    position: absolute;
    left: 0; right: 0;
    top: 45px;
    text-align: center;
    font-family: 'Poppins', sans-serif;
    font-weight: 600;
    font-size: 42px;
    line-height: 1;
    letter-spacing: -0.5px;
    color: var(--paper);
  }
  .band-blue   { background: var(--blue);   left: 17px; top: 13px; width: 299px; }
  .band-purple { background: var(--purple); left: 16px; top: 13px; width: 301px; height: 80px; }
  .band-green  { background: var(--green);  left: 18px; top: 16px; width: 298px; height: 79px; }
  .band-red    { background: var(--red);    left: 17px; top: 15px; width: 299px; height: 76px; }
  .band-red .suit-title { top: 43px; }

  .question {
    position: absolute;
    left: 0; right: 0;
    z-index: 2;
    text-align: center;
    font-family: 'Playfair Display', serif;
    font-style: italic;
    font-size: 19.5px;
    line-height: 22px;
    white-space: nowrap;
  }

  .back-frame {
    position: absolute;
    left: 17px; top: 15px;
    width: 298px; height: 204px;
    border: 1.6px solid;
  }
  .frame-blue   { border-color: var(--blue); }
  .frame-purple { border-color: var(--purple); }
  .frame-green  { border-color: var(--green); }
  .frame-red    { border-color: var(--red); }

  .sketch {
    position: absolute;
    z-index: 1;
    background: linear-gradient(135deg, #f2f0ed, var(--sketch));
    border-radius: 8px;
  }

  .letter {
    position: absolute;
    font-family: 'Poppins', sans-serif;
    font-size: 21.8px;
    line-height: 25.4px;
    white-space: nowrap;
    color: var(--ink);
  }
  .letter p { margin-bottom: 25.4px; }
  .letter strong { font-weight: 600; }
  .letter-left  { left: 460px; top: 636px; }
  .letter-right { left: 817px; top: 687px; }
</style>
</head>
<body>
<main class="sheet">

  <section class="card card-1">
    <div class="suit-band band-blue"><span class="suit-title">BOUNDARIES</span></div>
    <p class="question" style="top:132px; left:-4px;">What boundaries were crossed?</p>
  </section>

  <section class="card card-2">
    <div class="suit-band band-purple"><span class="suit-title">FANTASY</span></div>
    <p class="question" style="top:132px; left:-6px;">What was the dream you<br>imagined &nbsp;with this person?</p>
  </section>

  <section class="card card-3">
    <div class="suit-band band-green"><span class="suit-title">FORGIVENESS</span></div>
    <p class="question" style="top:129px; left:4px;">What are you still holding on to?</p>
    <div class="sketch" role="img" aria-label="Pencil sketch of a drifting feather" style="left:119px; top:166px; width:91px; height:59px;"></div>
  </section>

  <section class="card card-4">
    <div class="back-frame frame-blue"></div>
    <p class="question" style="top:84px; left:-20px;">What boundaries<br>are you drawing now?</p>
    <div class="sketch" role="img" aria-label="Pencil sketch of an 'occupied' door sign" style="left:216px; top:132px; width:83px; height:77px;"></div>
  </section>

  <section class="card card-5">
    <div class="back-frame frame-purple"></div>
    <p class="question" style="top:82px; left:-54px;">How did the<br>fantasy fall short?</p>
    <div class="sketch" role="img" aria-label="Line drawing of a crowned woman leaning in" style="left:214px; top:42px; width:97px; height:172px;"></div>
    <div class="sketch" role="img" aria-label="Line drawing of a frog sitting on an open hand" style="left:150px; top:140px; width:60px; height:74px;"></div>
  </section>

  <section class="card card-6">
    <div class="back-frame frame-green"></div>
    <p class="question" style="top:83px; left:-44px;">What are you willing<br>to let go of right now?</p>
    <div class="sketch" role="img" aria-label="Pencil sketch of a birdcage with its door open" style="left:244px; top:98px; width:70px; height:117px;"></div>
  </section>

  <section class="card card-7">
    <div class="suit-band band-red"><span class="suit-title">INCLUSION</span></div>
    <p class="question" style="top:131px; left:2px;">How did you include your<br>partner in your life?</p>
  </section>

  <section class="card card-8">
    <div class="back-frame frame-red"></div>
    <p class="question" style="top:69px; left:-64px;">What parts of your<br>life did you exclude<br>them from?</p>
    <div class="sketch" role="img" aria-label="Sketch of a woman kneeling and holding out a flower" style="left:224px; top:96px; width:90px; height:120px;"></div>
    <div class="sketch" role="img" aria-label="Sketch of a small child reaching for the flower" style="left:156px; top:142px; width:62px; height:72px;"></div>
  </section>

  <article class="letter letter-left">
    <p>Hi there,</p>
    <p>Please note that <strong>this is a<br>draft,</strong> –not the finished<br>product.<br>As illustration is a time<br>consuming practice, I have<br>done some small thumbnail<br>sketches to accompany<br>your lovely cards and<br>demonstrate my ideas.</p>
    <p>If my project is selected, I<br>will refine my drawings to a<br>greater calibre and work the<br>typography a little more too.</p>
  </article>

  <article class="letter letter-right">
    <p>I am considering adding a<br>subtle wash of watercolour<br>paint on the images too</p>
    <p>I decided to go with a<br>hand-drawn style because<br>it lends a sense of humanity<br>to the subject matter, and<br>celebrates imperfection.<br>-And we all can feel rather<br>imperfect after such an event<br>as a breakup!</p>
    <p>Cheers!</p>
  </article>

</main>
</body>
</html>
```